HOT TUB - SPAS service needs an business card

I need an business for my company who his specialise in a maintenance,water treatment and cleaning of Hot Tub - Spas for commercial and residential customers. The company operate mainly in the ski resort of Chamonix, Megève and St Gervais. The final product should communicate pure water, cleanest and professional for luxury property's.
I have upload a logo but any improvement on it is welcome.(color,size, details etc..) or any other idea. Thank you
Company Name: 58 BAINS
My name: Lucien Marchetti
Email: lucimarch@examplemail.net
Tel: +33 (0)6 71 58 29 64
Description to be on the card in french(first langage) and in English:
- Spas service
- Entretien, traitement eau, nettoyage.
- Maintenance, water treatment, cleaning.
Industry/Entity Type
Residential
Colors
Designer to choose colors to be used in the design.
Look and feel
Each slider illustrates characteristics of the customer's brand and the style your logo design should communicate.

```html
<!DOCTYPE html>
<html lang="fr">
<head>
<meta charset="utf-8">
<title>58 BAINS – Cartes de visite</title>
<link rel="stylesheet" href="https://fonts.googleapis.com/css2?family=Source+Sans+3:wght@400;600;700&display=swap">
<style>
  :root {
    --page-bg: #eef1f4;
    --card-blue: #2f8fdc;
    --card-blue-light: #4fa9ec;
    --card-blue-deep: #1f76c4;
    --ink-white: #ffffff;
    --shadow: rgba(20, 40, 70, 0.18);
  }
  * { margin: 0; padding: 0; box-sizing: border-box; }
  html, body {
    width: 1200px;
    height: 1127px;
    overflow: hidden;
    background: var(--page-bg);
    font-family: "Source Sans 3", "Myriad Pro", Arial, sans-serif;
    color: var(--ink-white);
  }
  .canvas { position: relative; width: 1200px; height: 1127px; }
  .card {
    position: absolute;
    width: 858px;
    height: 489px;
    overflow: hidden;
    box-shadow: 0 6px 18px var(--shadow);
  }
  .card--front { left: 306px; top: 50px; }
  .card--back  { left: 51px;  top: 585px; }
  .card__water {
    position: absolute; inset: 0;
    background:
      radial-gradient(ellipse at 70% 20%, var(--card-blue-light) 0%, transparent 60%),
      radial-gradient(ellipse at 15% 90%, var(--card-blue-deep) 0%, transparent 65%),
      var(--card-blue);
  }
  .brand-mark {
    position: absolute;
    display: flex; align-items: center; justify-content: center;
    font-weight: 600;
    letter-spacing: 0.04em;
    color: var(--ink-white);
  }
  .card--front .brand-mark { left: 47px; top: 30px; width: 546px; height: 146px; font-size: 64px; }
  .card--back  .brand-mark { left: 106px; top: 96px; width: 659px; height: 179px; font-size: 76px; }

  .company-name {
    position: absolute; left: 52px; top: 264px;
    font-size: 37px; font-weight: 600; letter-spacing: 0.01em;
  }
  .contact {
    position: absolute; left: 52px;
    display: flex; align-items: center; gap: 14px;
    font-size: 25px; font-weight: 400;
  }
  .contact--phone { top: 352px; }
  .contact--email { top: 402px; }
  .contact svg { width: 22px; height: 22px; flex: none; }
  .person-name {
    position: absolute; right: 45px; top: 347px;
    font-size: 33px; font-weight: 700;
  }

  .services {
    position: absolute; left: 0; right: 0; top: 283px;
    text-align: center;
  }
  .services__title { font-size: 29px; font-weight: 600; margin-bottom: 10px; }
  .services__list { font-size: 28px; font-weight: 400; line-height: 40px; }
</style>
</head>
<body>
<main class="canvas">

  <section class="card card--front" aria-label="Carte de visite, recto">
    <div class="card__water" role="img" aria-label="Gouttes d'eau sur fond bleu"></div>
    <div class="brand-mark">58 BAINS</div>
    <h1 class="company-name">58 BAINS</h1>
    <p class="contact contact--phone">
      <svg viewBox="0 0 24 24" aria-hidden="true"><path d="M6.6 2.5l3 3.2-1.9 2.6c1 2.4 3.4 4.9 6 6l2.6-1.9 3.2 3-2.2 3.1C10 18.3 5.7 14 4.5 4.7z" fill="none" stroke="#fff" stroke-width="1.8" stroke-linejoin="round"/></svg>
      +33 (0)6 71 58 29 64
    </p>
    <p class="contact contact--email">
      <svg viewBox="0 0 24 24" aria-hidden="true"><path d="M2 9l10-6 10 6v11H2z" fill="#fff"/><path d="M2 9l10 6 10-6" fill="none" stroke="#2f8fdc" stroke-width="1.6"/></svg>
      lucimarch@examplemail.net
    </p>
    <p class="person-name">Lucien Marchetti</p>
  </section>

  <section class="card card--back" aria-label="Carte de visite, verso">
    <div class="card__water" role="img" aria-label="Gouttes d'eau sur fond bleu"></div>
    <div class="brand-mark">58 BAINS</div>
    <div class="services">
      <h2 class="services__title">SPAS SERVICES</h2>
      <p class="services__list">•Entretien &nbsp;•traitement eau &nbsp;•nettoyage<br>•Maintenance &nbsp;•water treatment &nbsp;•cleaning.</p>
    </div>
  </section>

</main>
</body>
</html>
```